Walk Beside The River

Business Card design

Target Market(s)

People who require support in the commnity

Industry/Entity Type

Mental Health Support

Contact Information for Business Card

Mental Health Support Rosalind Tavener walkbesidetheriver@mailcove.com.au 0481 637 092 PO Box 926 Kestrel Bay QLD 4571

Colors
6B429C
8869AF
B7A5CE
E3DAEB
F3F0F8

Requirements
Must have
• Logo & details listed above
Should not have
• No red or orange

```html
<!DOCTYPE html>
<html lang="en">
<head>
<meta charset="utf-8">
<title>Walk Beside The River – Business Card</title>
<link rel="stylesheet" href="https://fonts.googleapis.com/css2?family=Open+Sans:wght@400;600;700;800&display=swap">
<style>
  :root {
    --stage: #232323;
    --card: #222124;
    --sun: #f2e92c;
    --violet: #6b429c;
    --violet-soft: #8869af;
    --ink: #ffffff;
    --pattern-light: #8d8d92;
    --pattern-dark: #1c1b1e;
  }
  * { box-sizing: border-box; margin: 0; padding: 0; }
  html, body {
    width: 1200px; height: 780px; overflow: hidden;
    background: var(--stage);
    font-family: "Open Sans", Arial, sans-serif;
  }
  .stage {
    width: 1200px; height: 780px;
    display: flex; align-items: center; justify-content: center; gap: 90px;
  }
  .card {
    position: relative;
    width: 360px; height: 600px;
    background: var(--card);
    border-left: 6px solid var(--sun);
    box-shadow: 0 18px 40px rgba(0,0,0,.55);
    overflow: hidden;
  }
  /* front */
  .card-front__pattern {
    position: absolute; inset: 0;
    background: linear-gradient(135deg, var(--pattern-light) 0%, #4a4a4f 22%, var(--pattern-dark) 45%, var(--pattern-dark) 100%);
  }
  .card-front__name {
    position: absolute; left: 0; right: 0; top: 50%;
    transform: translateY(-50%);
    text-align: center;
    color: var(--sun);
    font-weight: 800; font-size: 30px; line-height: 1.15;
  }
  /* back */
  .brand {
    position: absolute; top: 70px; left: 0; right: 0;
    display: flex; align-items: center; justify-content: center; gap: 14px;
  }
  .brand__dot {
    width: 46px; height: 46px; border-radius: 50%;
    background: var(--violet);
  }
  .brand__name {
    color: var(--violet-soft);
    font-weight: 700; font-size: 19px; line-height: 1.2;
  }
  .person {
    position: absolute; top: 325px; right: 34px; text-align: right;
  }
  .person__name { font-weight: 800; font-size: 30px; line-height: 1.1; white-space: nowrap; }
  .person__first { color: var(--sun); }
  .person__last { color: var(--violet-soft); }
  .person__role { color: var(--ink); font-size: 15px; font-weight: 600; margin-top: 4px; }
  .details {
    position: absolute; left: 34px; right: 20px; bottom: 66px;
    color: var(--ink); font-size: 15px; line-height: 1.35;
  }
  .details__org { margin-bottom: 16px; }
  .contact { list-style: none; }
  .contact li { display: flex; align-items: center; gap: 9px; margin-top: 4px; white-space: nowrap; }
  .contact svg { width: 15px; height: 15px; flex: none; }
</style>
</head>
<body>
<main class="stage">
  <section class="card card-front">
    <div class="card-front__pattern" role="img" aria-label="Repeating star pattern fading from silver at the top left to black"></div>
    <p class="card-front__name">Walk Beside<br>The River</p>
  </section>

  <section class="card card-back">
    <div class="brand">
      <span class="brand__dot"></span>
      <span class="brand__name">Walk Beside<br>The River</span>
    </div>

    <div class="person">
      <h1 class="person__name"><span class="person__first">Mirela</span> <span class="person__last">Vostrova</span></h1>
      <p class="person__role">CEO/Director</p>
    </div>

    <div class="details">
      <p class="details__org">Mental Health Support<br>Rosalind Tavener</p>
      <ul class="contact">
        <li>
          <svg viewBox="0 0 24 24" aria-hidden="true"><path fill="var(--sun)" d="M6.6 10.8a15 15 0 0 0 6.6 6.6l2.2-2.2a1 1 0 0 1 1-.25 11.4 11.4 0 0 0 3.6.6 1 1 0 0 1 1 1V20a1 1 0 0 1-1 1A17 17 0 0 1 3 4a1 1 0 0 1 1-1h3.5a1 1 0 0 1 1 1c0 1.25.2 2.45.6 3.6a1 1 0 0 1-.25 1z"/></svg>
          0481 637 092
        </li>
        <li>
          <svg viewBox="0 0 24 24" aria-hidden="true"><path fill="none" stroke="var(--sun)" stroke-width="2" d="M3 6h18v12H3z M3 6l9 7 9-7"/></svg>
          walkbesidetheriver@mailcove.com.au
        </li>
        <li>
          <svg viewBox="0 0 24 24" aria-hidden="true"><path fill="var(--sun)" d="M12 2a7 7 0 0 0-7 7c0 5 7 13 7 13s7-8 7-13a7 7 0 0 0-7-7zm0 9.5A2.5 2.5 0 1 1 12 6.5a2.5 2.5 0 0 1 0 5z"/></svg>
          PO Box 926 Kestrel Bay QLD 4571
        </li>
      </ul>
    </div>
  </section>
</main>
</body>
</html>
```